Local Chiropractor Needs Up Scale Webdesign

This website needs to have an upscale look with a very modern feel. Below is the information and websites to reference

Add Logo that is attached

Build a color scheme similar to this website image titled "chiro-1"

Must Include these pages in a horizontal menu bar in this order:
Home, Meet Our Staff, Patient Testimonials, Videos, Work Place Wellness, Contact

Build a "classy looking" Make An Appointment Button into the header with the contact info below

Phone Number:
555-314-2719

Address:
3168 Pelham Orchard Lane, #240
Chanhassen, MN 55317

This website needs 4 rotating banners. Please reference a layout similar to this for the banners: http://drmorlatz.example/. However design it nicer than this website, this website is very boring and doesn't flow with the colors properly

Below are the description for each banner

Rotating Banner #1
Use Image: Pediatrics
Two lines of text. First line title line, second description. Use Latin text for fill

Rotating Banner #2
Use Image: Aging Gracefully

Rotating Banner #3
Use Image: Pregnancy

Rotating Banner #4
Use Image: Athletics

I'd like to see a free consultation box similar to the "chiro-1" image. Fields to include are: First Name, Last Name, Phone Number, Comments.

For the body, please fill it with latin text. Please design a professional body layout. You can include a box in the right column for the hours

Office Hours
Monday: 8:00-11:00, 2:00-5:00
Tuesday: 8:30-11:00, 2:00-5:30
Wednesday: 8:00-11:00, 2:00-5:00
Thursday: 10:00-12:00, 2:30-5:00
Friday: 8:00-10:00, 1:00-5:00
Saturday: Closed
Sunday: Closed

For the footer please design something similar to the: http://drmorlatz.example/

Also include in the Footer: Powered by Brightline Site Works

```html
<!DOCTYPE html>
<html lang="en">
<head>
<meta charset="utf-8">
<title>Evergreen Path Chiropractic Health Center</title>
<link rel="stylesheet" href="https://fonts.googleapis.com/css2?family=Cormorant+Garamond:ital,wght@0,500;1,500&family=Mulish:wght@400;600;700&display=swap">
<style>
:root{
  --ink:#1f1f1f;
  --header:#262626;
  --nav:#0b0b0b;
  --footer:#252525;
  --gold:#c98f1b;
  --leaf:#8cc63f;
  --green:#3f7a3a;
  --muted:#cfcfcf;
  --white:#ffffff;
  --rule:#5a5a5a;
}
*{box-sizing:border-box;margin:0;padding:0}
html,body{width:694px;height:1200px;overflow:hidden;background:var(--white)}
body{font-family:"Mulish",sans-serif;color:var(--ink);position:relative}
.site-header{position:absolute;left:0;top:0;width:694px;height:64px;background:var(--header);color:var(--white)}
.brand{position:absolute;left:16px;top:8px;display:flex;align-items:center;gap:8px}
.brand-dot{width:34px;height:34px;border-radius:50%;background:var(--leaf)}
.brand-name{color:var(--leaf);font-size:15px;font-weight:600;line-height:1.05;width:148px}
.header-address{position:absolute;left:215px;top:31px;font-size:10px;line-height:16px;letter-spacing:.4px}
.header-address span{display:block}
.header-address span:first-child{margin-top:-16px}
.header-phone{position:absolute;left:376px;top:30px;font-size:8px;letter-spacing:.5px}
.header-phone b{font-size:12px;font-weight:400;margin-left:4px;letter-spacing:.6px}
.appointment{position:absolute;left:535px;top:18px;height:34px;padding-left:7px;border-left:2px solid var(--white)}
.appointment a{display:block;width:121px;height:26px;margin-top:3px;background:var(--gold);color:var(--white);font-size:9px;font-weight:700;letter-spacing:.5px;text-align:center;line-height:26px;text-decoration:none}
.main-nav{position:absolute;left:0;top:64px;width:694px;height:54px;background:linear-gradient(#1a1a1a,var(--nav));border-top:2px solid #d9d9d9;border-bottom:2px solid var(--gold)}
.main-nav ul{list-style:none;display:flex;position:absolute;top:19px;left:30px}
.main-nav li{font-size:10px;letter-spacing:.8px;color:var(--white);border-right:1px solid #bbb;padding:0 6px;line-height:14px}
.main-nav li.active{color:var(--leaf)}
.main-nav li+li{margin-left:4px;border-left:1px solid #bbb}
.hero{position:absolute;left:0;top:118px;width:694px;height:434px;background:#eeeeee;border-bottom:3px solid #d8d8d8}
.hero-photo{position:absolute;left:0;top:22px;width:694px;height:410px;background:linear-gradient(180deg,#4d6b2f 0%,#7a8f52 45%,#9a8a66 80%,#b9a584 100%)}
.hero-arrow{position:absolute;top:232px}
.consult-tab{position:absolute;left:0;top:0}
.consult-tab span{position:absolute;left:36px;top:18px;color:var(--white);font-size:14.5px;font-weight:600;white-space:nowrap}
.slide-title{position:absolute;left:142px;top:294px;width:485px;height:48px;background:rgba(255,255,255,.82);text-align:center;font-family:"Cormorant Garamond",serif;color:var(--green);font-size:38px;line-height:48px;letter-spacing:1.5px}
.slide-text{position:absolute;left:30px;top:350px;width:634px;height:54px;background:rgba(255,255,255,.78);text-align:center;font-family:"Cormorant Garamond",serif;font-style:italic;color:var(--green);font-size:21.5px;line-height:54px}
.intro{position:absolute;left:40px;top:592px;width:318px}
.intro h1{font-size:20px;font-weight:400;margin-left:18px;margin-bottom:24px}
.intro p{font-size:13.6px;line-height:19.5px;text-align:justify;letter-spacing:.3px}
.hours-card{position:absolute;left:426px;top:577px;width:248px;height:356px;border:2px solid var(--green);padding:3px}
.hours-inner{border:1px solid var(--green);height:100%;padding:24px 0 0 21px}
.hours-inner h2{font-size:16px;font-weight:400;margin-bottom:20px}
.hours-inner p{font-size:12.6px;line-height:39px;margin-top:-8px}
.hours-inner p b{font-weight:600}
.site-footer{position:absolute;left:0;top:962px;width:694px;height:238px;background:var(--footer);color:var(--white)}
.footer-title{font-size:12px;letter-spacing:1.3px;padding-bottom:3px;border-bottom:1px solid #9a9a9a;display:inline-block;font-weight:400}
.footer-contact{position:absolute;left:26px;top:30px}
.footer-contact .small{font-size:10px;letter-spacing:.5px;margin-top:14px}
.footer-contact .small b{font-weight:400;font-size:14px;margin-left:4px;letter-spacing:.8px}
.footer-contact .addr{font-size:12.5px;line-height:19px;letter-spacing:.6px;margin-top:2px}
.footer-map{position:absolute;left:282px;top:32px;width:139px;height:139px;background:linear-gradient(135deg,#e6e1cf,#d9d3b8 60%,#c8d6b0)}
.footer-hours{position:absolute;left:489px;top:30px}
.footer-hours ul{list-style:none;margin-top:12px;font-size:9.8px;letter-spacing:.8px;line-height:18.7px}
.footer-base{position:absolute;left:0;top:204px;width:694px;border-top:1px solid var(--rule);padding:10px 0 0 24px;font-size:8px;color:var(--muted);letter-spacing:.4px}
</style>
</head>
<body>
<header class="site-header">
  <div class="brand"><span class="brand-dot"></span><span class="brand-name">Evergreen Path Chiropractic</span></div>
  <div class="header-address"><span>3168 Pelham Orchard Lane, #240</span><span>Chanhassen, MN 55317</span></div>
  <div class="header-phone">Phone number: <b>555-314-2719</b></div>
  <div class="appointment"><a href="#">MAKE AN APOINTMENT</a></div>
</header>
<nav class="main-nav">
  <ul>
    <li class="active">HOME</li><li>MEET OUR STAFF</li><li>PATIENT TESTEMONIALS</li><li>VIDEOS</li><li>WORK PLACE WELLNESS</li><li>CONTACT</li>
  </ul>
</nav>
<section class="hero">
  <div class="hero-photo" role="img" aria-label="Two senior women jogging on a forest trail"></div>
  <svg class="hero-arrow" style="left:6px" width="20" height="56" viewBox="0 0 20 56"><path d="M17 2 L4 28 L17 54" fill="none" stroke="rgba(255,255,255,.6)" stroke-width="2"/></svg>
  <svg class="hero-arrow" style="left:668px" width="20" height="56" viewBox="0 0 20 56"><path d="M3 2 L16 28 L3 54" fill="none" stroke="rgba(255,255,255,.6)" stroke-width="2"/></svg>
  <div class="consult-tab">
    <svg width="226" height="98" viewBox="0 0 226 98"><path d="M0 0 H226 V50 L113 97 L0 50 Z" fill="#2b2b2b"/><path d="M0 4 H222 V48 L113 93 L0 48" fill="none" stroke="#6d6d6d" stroke-width="1"/></svg>
    <span>CONSULTATION BOX</span>
  </div>
  <div class="slide-title">— AGING GRACEFULLY —</div>
  <div class="slide-text">”Lorem ipsum dolor sit amet, consectetur adipiscing elit sed do …”</div>
</section>
<main>
  <article class="intro">
    <h1>Lorem ipsum dolor sit amet</h1>
    <p>Lorem ipsum dolor sit amet, consectetur adipiscing elit. Integer nec odio. Praesent libero. Sed cursus ante dapibus diam. Sed nisi. Nulla quis sem at nibh elementum imperdiet. Duis sagittis ipsum. Praesent mauris. Fusce nec tellus sed augue semper porta. Mauris massa. Vestibulum lacinia arcu eget nulla. Class aptent taciti sociosqu ad litora torquent per conubia nostra, per inceptos himenaeos. Curabitur sodales porttitor. Morbi lectus risus, iaculis vel, suscipit quis, luctus non, massa. Fusce ac turpis quis ullamcorper.</p>
  </article>
  <aside class="hours-card">
    <div class="hours-inner">
      <h2>Office Hours</h2>
      <p><b>Monday:</b> 8:00-11:00, 2:00-5:00</p>
      <p><b>Tuesday:</b> 8:30-11:00, 2:00-5:30</p>
      <p><b>Wednesday:</b> 8:00-11:00, 2:00-5:00</p>
      <p><b>Thursday:</b> 10:00-12:00, 2:30-5:00</p>
      <p><b>Friday:</b> 8:00-10:00, 1:00-5:00</p>
      <p><b>Saturday:</b> Closed</p>
      <p><b>Sunday:</b> Closed</p>
    </div>
  </aside>
</main>
<footer class="site-footer">
  <div class="footer-contact">
    <h3 class="footer-title">CONTACT</h3>
    <p class="small">Phone number: <b>555-314-2719</b></p>
    <p class="small" style="margin-top:6px">Adress:</p>
    <p class="addr">3168 Pelham Orchard Lane, #240<br>Chanhassen, MN 55317</p>
  </div>
  <div class="footer-map" role="img" aria-label="Street map showing the office location"></div>
  <div class="footer-hours">
    <h3 class="footer-title">OFFICE HOURS</h3>
    <ul>
      <li>Monday: 8:00-11:00, 2:00-5:00</li>
      <li>Tuesday: 8:30-11:00, 2:00-5:30</li>
      <li>Wednesday: 8:00-11:00, 2:00-5:00</li>
      <li>Thursday: 10:00-12:00, 2:30-5:00</li>
      <li>Friday: 8:00-10:00, 1:00-5:00</li>
      <li>Saturday: Closed</li>
      <li>Sunday: Closed</li>
    </ul>
  </div>
  <div class="footer-base">Powered by Brightline Site Works</div>
</footer>
</body>
</html>
```